Velk Partners Building Business Cards

We need a business card that reflects our business as "Solar Experts" in San Diego. Browse our website www.velkpartners.example our License needs to be displayed as "CSLB# 3867140" our phone number is (619) 555-0187

Save thousands on your electric bills and increase the value of your home while helping to protect the environment. Our solar installation experts will help you design the system that's right for you, using only the highest quality equipment that will look great and give you ideal performance. Our goal is to make you energy independent, and get your electric bill to 0.

Paul Osterby
(619) 555-0187
paul@velkpartners.example

Target Market(s)

Home owners in san diego looking for solar

Industry/Entity Type

Solar Energy

Contact Information for Business Card

Paul Osterby
(619) 555-0187
paul@velkpartners.example

Font styles to use
Other font styles liked:
• Use our logo font

Requirements
Must have
• License needs to be displayed as "CSLB# 3867140" our phone number is (619) 555-0187
Nice to have
• Real images of rooftop home solar in san diego
Should not have
• our business address

```html
<!DOCTYPE html>
<html lang="en">
<head>
<meta charset="utf-8">
<title>Velk Partners Building – Business Cards</title>
<link rel="stylesheet" href="https://fonts.googleapis.com/css2?family=Open+Sans:wght@400;600;700&display=swap">
<style>
  :root {
    --navy: #1d3c78;
    --sun: #f6ac0c;
    --white: #ffffff;
    --backdrop: #eceae6;
    --panel-blue: #2f4f9a;
    --panel-deep: #1c2f66;
    --panel-sky: #c9d4ea;
  }
  * { margin: 0; padding: 0; box-sizing: border-box; }
  html, body { width: 1200px; height: 900px; overflow: hidden; }
  body {
    position: relative;
    background: var(--backdrop);
    font-family: "Open Sans", Arial, sans-serif;
  }
  .card {
    position: absolute;
    background: var(--white);
    overflow: hidden;
    box-shadow: 0 6px 18px rgba(0,0,0,0.18);
  }
  .card--front { left: 238px; top: 62px; width: 555px; height: 342px; }
  .card--back  { left: 459px; top: 519px; width: 560px; height: 343px; }

  .front-artwork {
    position: absolute;
    left: 0; right: 0; bottom: 0; height: 190px;
    background: linear-gradient(180deg, var(--navy) 0%, var(--navy) 14%, var(--white) 14%, var(--white) 18%, var(--sun) 18%, var(--sun) 100%);
  }
  .holder-name {
    position: absolute;
    right: 30px; top: 70px;
    color: var(--navy);
    font-weight: 700;
    font-size: 21px;
    letter-spacing: 0.2px;
  }
  .contact-list {
    position: absolute;
    right: 30px; top: 238px;
    list-style: none;
    text-align: right;
    color: var(--white);
    font-size: 15px;
    line-height: 1.45;
  }
  .contact-list li { display: flex; justify-content: flex-end; align-items: center; gap: 7px; }
  .contact-list .license { font-size: 15.5px; margin-bottom: 7px; }
  .license-label { color: var(--navy); font-weight: 700; }
  .contact-icon { width: 12px; height: 12px; fill: var(--navy); }

  .company-name {
    position: absolute;
    left: 0; right: 0; top: 52px;
    text-align: center;
    color: var(--navy);
    font-weight: 700;
    font-size: 40px;
    letter-spacing: -0.5px;
  }
  .rooftop-photo {
    position: absolute;
    left: 0; right: 0; bottom: 0; height: 200px;
    background: linear-gradient(180deg, var(--white) 0%, var(--panel-sky) 18%, var(--panel-blue) 45%, var(--panel-deep) 100%);
  }
</style>
</head>
<body>
  <section class="card card--front">
    <div class="front-artwork" role="img" aria-label="Sun rising over a blue wave on a golden field"></div>
    <h1 class="holder-name">PAUL OSTERBY</h1>
    <ul class="contact-list">
      <li class="license"><span><span class="license-label">License:</span> CSLB# 3867140</span></li>
      <li>(619) 555-0187
        <svg class="contact-icon" viewBox="0 0 24 24" aria-hidden="true"><path d="M6.6 10.8a15.1 15.1 0 0 0 6.6 6.6l2.2-2.2a1 1 0 0 1 1-.25 11.4 11.4 0 0 0 3.6.57 1 1 0 0 1 1 1V20a1 1 0 0 1-1 1A17 17 0 0 1 3 4a1 1 0 0 1 1-1h3.5a1 1 0 0 1 1 1c0 1.25.2 2.45.57 3.57a1 1 0 0 1-.25 1z"/></svg>
      </li>
      <li>paul@velkpartners.example
        <svg class="contact-icon" viewBox="0 0 24 24" aria-hidden="true"><path d="M3 6h18v12H3z" fill="none"/><path d="M3 6h18v1.5l-9 6-9-6z"/><path d="M3 9.3l9 6 9-6V18H3z"/></svg>
      </li>
    </ul>
  </section>

  <section class="card card--back">
    <h2 class="company-name">Velk Partners Building</h2>
    <div class="rooftop-photo" role="img" aria-label="Photograph of rows of rooftop solar panels"></div>
  </section>
</body>
</html>
```